Computer consultant business card

Zorqa Software is a newly started computer consulting company. It's a small one-man company that provides mostly Vornix applications but also websites in collaboration with designers. I'm running this company on the side of full time university studies.

I want the final design to be clean and memorable. Be creative! :)

Some inspiration:
http://www.pixelmarta.com/design/48317
http://www.pixelmarta.com/design/2739164/business-card-design-by-frostlynk
http://www.pixelmarta.com/design/604281/business-card-design-by-koralind-vestrabanu

See attachment for my company logo.
Updates

I would like to thank everyone for submitting! I'll need a couple of days to review and ultimately select a design.

Target Market(s)

Non-technical entrepreneurs and small companies.

Industry/Entity Type

University

Requirements
Must have
• My company logo.
In any way, both colors from my logo.
First- and last name, e-mail and phone number.
Double-sided design.
Nice to have
• Something creative with the symbol in my logo

```html
<!DOCTYPE html>
<html lang="en">
<head>
<meta charset="utf-8">
<title>Zorqa Software – Business Card</title>
<link rel="stylesheet" href="https://fonts.googleapis.com/css2?family=Arimo:wght@400;700&display=swap">
<style>
  :root {
    --stage-light: #9a9a9a;
    --stage-dark: #5a5a5a;
    --brand-blue: #4473c0;
    --brand-blue-deep: #3d68b3;
    --brand-ink: #2d2c30;
    --card-white: #ffffff;
    --link-cyan: #5ec3ee;
    --text-dark: #1f1f24;
  }
  * { box-sizing: border-box; margin: 0; padding: 0; }
  html, body { width: 1200px; height: 787px; overflow: hidden; }
  body {
    background: radial-gradient(ellipse at 50% 35%, var(--stage-light), var(--stage-dark));
    font-family: "Arimo", Arial, sans-serif;
    position: relative;
  }
  .card {
    position: absolute;
    top: 244px;
    width: 510px;
    height: 300px;
    box-shadow: 0 10px 24px rgba(0,0,0,.35);
    overflow: hidden;
  }

  /* Front */
  .card-front { left: 50px; background: linear-gradient(160deg, #4c7ec9, var(--brand-blue-deep)); }
  .card-front .wordmark {
    position: absolute; left: 120px; top: 100px;
    display: flex; align-items: center; gap: 18px;
  }
  .wordmark .mark-dot {
    flex: none;
    width: 70px; height: 70px; border-radius: 50%;
    background: var(--brand-ink);
  }
  .wordmark .mark-name {
    font-weight: 700; font-size: 64px; color: var(--brand-ink); letter-spacing: 1px;
    line-height: 1;
  }
  .card-front .underline {
    position: absolute; left: 220px; right: 0; top: 196px;
    height: 4px; background: var(--card-white);
  }

  /* Back */
  .card-back {
    left: 640px; background: var(--brand-blue);
    padding: 12px 12px 0;
  }
  .card-back .sheet {
    position: relative; width: 100%; height: 100%;
    background: var(--card-white);
  }
  .card-back .wordmark {
    position: absolute; left: 20px; top: 66px;
    display: flex; align-items: center; gap: 10px;
  }
  .card-back .mark-dot { width: 40px; height: 40px; }
  .card-back .mark-name { font-size: 36px; }

  .identity { position: absolute; right: 14px; top: 76px; text-align: right; }
  .identity .person { font-size: 22px; color: var(--brand-blue); line-height: 1.1; }
  .identity .role { font-size: 12px; font-weight: 700; color: var(--brand-blue); letter-spacing: .5px; margin-top: 4px; }
  .rule { position: absolute; left: 20px; right: 0; top: 130px; height: 4px; background: var(--brand-blue); }

  .contacts { position: absolute; left: 20px; right: 14px; top: 142px; font-size: 11px; font-weight: 700; }
  .contacts .row { display: flex; justify-content: space-between; margin-bottom: 6px; }
  .contacts .phone { color: var(--text-dark); }
  .contacts .link { color: var(--link-cyan); }

  .footer-band { position: absolute; left: 0; right: 0; bottom: 0; height: 56px; }
  .footer-band svg.band-shape { position: absolute; inset: 0; width: 100%; height: 100%; }
  .footer-items {
    position: absolute; left: 20px; bottom: 10px;
    display: flex; align-items: center; gap: 14px;
    font-size: 10px; line-height: 1; color: var(--card-white);
  }
  .footer-items .divider { width: 1px; height: 16px; background: rgba(255,255,255,.6); }
  .footer-items .item { display: flex; align-items: center; gap: 6px; }
</style>
</head>
<body>

<section class="card card-front" aria-label="Card front">
  <div class="wordmark">
    <span class="mark-dot"></span>
    <span class="mark-name">zorqa</span>
  </div>
  <div class="underline"></div>
</section>

<section class="card card-back" aria-label="Card back">
  <div class="sheet">
    <div class="wordmark">
      <span class="mark-dot"></span>
      <span class="mark-name">zorqa</span>
    </div>

    <div class="identity">
      <p class="person">Your name</p>
      <p class="role">MANAGER DIRECTOR</p>
    </div>
    <div class="rule"></div>

    <div class="contacts">
      <div class="row phone">
        <span>P : +(000) 123 456 789</span>
        <span>F : +(000) 123 456 789</span>
      </div>
      <div class="row link">
        <span>chirpline.net/ourcompany</span>
        <span>friendwall.net/ourcompany</span>
      </div>
    </div>

    <div class="footer-band">
      <svg class="band-shape" viewBox="0 0 486 56" preserveAspectRatio="none" aria-hidden="true">
        <path d="M0 20 H400 Q418 20 428 10 Q438 0 456 0 H486 V56 H0 Z" fill="#4473c0"/>
      </svg>
      <div class="footer-items">
        <span class="item">
          <svg width="12" height="12" viewBox="0 0 12 12" aria-hidden="true"><circle cx="6" cy="6" r="5" fill="none" stroke="#fff" stroke-width="1.2"/><path d="M1 6h10M6 1c-2 3-2 7 0 10M6 1c2 3 2 7 0 10" fill="none" stroke="#fff" stroke-width="1"/></svg>
          www.company.com
        </span>
        <span class="divider"></span>
        <span class="item">
          <svg width="12" height="12" viewBox="0 0 12 12" aria-hidden="true"><circle cx="6" cy="6" r="5" fill="none" stroke="#fff" stroke-width="1.2"/><circle cx="6" cy="6" r="2" fill="none" stroke="#fff" stroke-width="1.2"/></svg>
          info@company.com
        </span>
      </div>
    </div>
  </div>
</section>

</body>
</html>
```